Law Offices business card

Hi there, I'll need business card for the Law Offices of Colin Matheny. The information must convey his strategic approach and quick resolution to complex business litigation needs. Please emphasize Civil Litigation, Corporate Law, Business Governance and Real Estate Law. Colin has over 25 years of experience in these fields.The card should be modern and edgy and the message should be clear. Please consult his current website for ideas.

```html
<!DOCTYPE html>
<html lang="en">
<head>
<meta charset="utf-8">
<title>Law Offices of Colin Matheny – Business Card</title>
<link href="https://fonts.googleapis.com/css2?family=Lato:wght@400;700&display=swap" rel="stylesheet">
<style>
  :root {
    --backdrop: #8f8f90;
    --ink: #0b0b0b;
    --brand-red: #9e3d3f;
    --paper: #f1efef;
    --soft-text: #efe3e3;
  }
  * { box-sizing: border-box; margin: 0; padding: 0; }
  html, body {
    width: 1105px; height: 1200px; overflow: hidden;
    background: var(--backdrop);
    font-family: "Lato", "Helvetica Neue", Arial, sans-serif;
  }
  .canvas { position: relative; width: 1105px; height: 1200px; }
  .card {
    position: absolute; left: 182px; width: 746px; height: 427px;
    overflow: hidden; background: var(--brand-red);
  }
  .card--front { top: 119px; }
  .card--back { top: 637px; }

  .front__header {
    position: absolute; left: 0; top: 0; width: 100%; height: 222px;
    background: var(--ink);
    border-bottom: 4px solid var(--paper);
    display: flex; align-items: center; justify-content: center;
  }
  .wordmark {
    display: flex; align-items: center; gap: 14px;
    color: var(--paper); font-weight: 400;
    font-size: 34px; letter-spacing: 1px;
  }
  .wordmark__square { width: 14px; height: 14px; background: var(--paper); }

  .contact {
    position: absolute; top: 270px; left: 0; width: 100%;
    display: flex; color: var(--soft-text);
  }
  .contact__identity {
    width: 354px; text-align: right;
    font-size: 18.5px; line-height: 28px;
  }
  .contact__name { font-size: 21px; letter-spacing: 0.5px; line-height: 30px; }
  .contact__divider {
    width: 1px; height: 108px; margin: 10px 26px 0 26px;
    background: var(--soft-text); opacity: 0.8;
  }
  .contact__lines { list-style: none; font-size: 18.5px; line-height: 28.5px; }
  .contact__lines li { display: flex; align-items: center; gap: 12px; }
  .contact__lines svg { width: 18px; height: 18px; fill: var(--soft-text); }

  .back__name {
    position: absolute; top: 110px; width: 100%; text-align: center;
    color: var(--paper); font-size: 30px; letter-spacing: 6px; font-weight: 400;
  }
  .back__rule {
    position: absolute; top: 168px; left: 343px; width: 60px; height: 1px;
    background: var(--soft-text);
  }
  .practice-areas {
    position: absolute; top: 192px; width: 100%; text-align: center;
    list-style: none; color: var(--soft-text);
    font-size: 16px; letter-spacing: 2px; line-height: 28px;
  }
  .practice-areas li { display: inline; }
  .practice-areas li + li::before { content: "·"; margin: 0 12px; }
  .practice-areas__break { display: block; }
  .experience {
    position: absolute; top: 262px; width: 100%; text-align: center;
    color: var(--paper); font-size: 16px; letter-spacing: 2px; font-weight: 700;
  }
  .back__url {
    position: absolute; top: 347px; width: 100%; text-align: center;
    color: var(--soft-text); font-size: 21px; letter-spacing: 5px;
  }
</style>
</head>
<body>
<main class="canvas">
  <section class="card card--front">
    <header class="front__header">
      <div class="wordmark">
        <span class="wordmark__square"></span>
        <span class="wordmark__name">Law Offices of Colin Matheny, PA</span>
      </div>
    </header>
    <div class="contact">
      <div class="contact__identity">
        <p class="contact__name">COLIN MATHENY</p>
        <p>ATTORNEY</p>
        <p>118B Harbor Lane</p>
        <p>Coral Bay, Florida 33012</p>
      </div>
      <div class="contact__divider"></div>
      <ul class="contact__lines">
        <li><svg viewBox="0 0 24 24" aria-hidden="true"><path d="M6.6 10.8a15 15 0 0 0 6.6 6.6l2.2-2.2a1 1 0 0 1 1-.25 11.4 11.4 0 0 0 3.6.57 1 1 0 0 1 1 1V20a1 1 0 0 1-1 1A17 17 0 0 1 3 4a1 1 0 0 1 1-1h3.5a1 1 0 0 1 1 1c0 1.25.2 2.45.57 3.57a1 1 0 0 1-.25 1z"/></svg>555-201-4830</li>
        <li><svg viewBox="0 0 24 24" aria-hidden="true"><path d="M6 2h12v5H6zM3 8h18a1 1 0 0 1 1 1v8h-4v5H6v-5H2V9a1 1 0 0 1 1-1zm5 8v4h8v-4z"/></svg>555-201-4831</li>
        <li><svg viewBox="0 0 24 24" aria-hidden="true"><path d="M2 5h20v14H2zm2 2v.5l8 5 8-5V7z"/></svg>colin@mathenylaw.com</li>
        <li><svg viewBox="0 0 24 24" aria-hidden="true"><path d="M12 2a10 10 0 1 0 0 20 10 10 0 0 0 0-20zm1 17.9V17h-2v-2l-5-5 .3-2A8 8 0 0 1 15 4.6V6h-2v2l-2 2 4 3h3l1.6 2.3A8 8 0 0 1 13 19.9z"/></svg>www.mathenylaw.com</li>
      </ul>
    </div>
  </section>

  <section class="card card--back">
    <p class="back__name">COLIN MATHENY</p>
    <span class="back__rule"></span>
    <div class="practice-areas">
      <ul>
        <li>CIVIL LITIGATION</li>
        <li>CORPORATE LAW</li>
      </ul>
      <ul>
        <li>BUSINESS GOVERNANCE</li>
        <li>REAL ESTATE LAW</li>
      </ul>
    </div>
    <p class="experience">OVER 25 YEARS OF EXPERIENCE</p>
    <p class="back__url">WWW.MATHENYLAW.COM</p>
  </section>
</main>
</body>
</html>
```